Business Card for my New Brokerage

Looking to get a business card design for my new Real Estate Brokerage.
I want it with Picture, Phone Number, Email, Website, Office Address
Name and Designation. Please add logo too.

Target Market(s)

Real Estate Investors or Home Buyers

Industry/Entity Type

Real Estate

Contact Information for Business Card

Name, Email, Phone Number, website, email, office address

Colors
EB3D1F
EC4F4E
F09395
F8D3D4
FCEDEE

Requirements
Must have
• Minimalistic, Clean, Modern, Photo
Nice to have
• White and Red Colors

```html
<!DOCTYPE html>
<html lang="en">
<head>
<meta charset="utf-8">
<title>Ember Realty Inc – Business Card</title>
<link rel="stylesheet" href="https://fonts.googleapis.com/css2?family=Montserrat:ital,wght@0,400;0,500;0,700;0,800;1,400&display=swap">
<style>
  :root {
    --brand-red: #e10a0a;
    --ink: #333333;
    --card: #ffffff;
    --backdrop: #1c1c1c;
    --photo-light: #c9b8a8;
    --photo-dark: #2a2f3a;
  }
  * { margin: 0; padding: 0; box-sizing: border-box; }
  html, body {
    width: 1200px; height: 900px; overflow: hidden;
    background: var(--backdrop);
    font-family: "Montserrat", Arial, sans-serif;
  }
  .card {
    position: absolute; left: 100px; top: 165px;
    width: 1000px; height: 570px;
    background: var(--card);
    border-radius: 36px;
    overflow: hidden;
  }
  .card__band { position: absolute; left: 0; top: 0; }
  .card__photo {
    position: absolute; left: 175px; top: 28px;
    width: 190px; height: 190px; border-radius: 50%;
    border: 3px solid var(--brand-red);
    background: radial-gradient(circle at 50% 38%, var(--photo-light) 0 30%, #ffffff 31% 55%, var(--photo-dark) 56%);
  }
  .card__accent {
    position: absolute; left: 0; top: 232px;
    width: 8px; height: 40px; background: var(--brand-red);
  }
  .person { position: absolute; left: 62px; top: 232px; }
  .person__name {
    font-weight: 800; font-size: 40px; letter-spacing: 1px;
    color: var(--brand-red); text-transform: uppercase;
  }
  .person__role {
    font-size: 25px; color: var(--ink); margin-top: 2px; letter-spacing: .5px;
  }
  .card__rule {
    position: absolute; left: 42px; right: 52px; top: 330px;
    height: 2px; background: var(--brand-red);
  }
  .contact { position: absolute; left: 42px; top: 345px; list-style: none; }
  .contact__item {
    display: flex; align-items: center; gap: 12px;
    font-size: 23px; color: var(--ink); line-height: 36px;
    font-style: italic;
  }
  .contact__item svg { width: 18px; height: 18px; flex: none; }
  .brand {
    position: absolute; left: 610px; top: 190px;
    display: flex; align-items: center; gap: 16px;
    color: var(--brand-red); font-weight: 800;
    font-size: 50px; letter-spacing: 2px; line-height: 1;
  }
  .brand__mark { width: 18px; height: 18px; background: var(--brand-red); }
  .address {
    position: absolute; right: 60px; bottom: 58px;
    font-size: 24px; color: var(--ink); line-height: 36px; letter-spacing: .5px;
  }
</style>
</head>
<body>
  <main class="card">
    <svg class="card__band" width="1000" height="200" viewBox="0 0 1000 200" aria-hidden="true">
      <polygon points="0,0 470,0 470,95 380,200 0,200 0,0" fill="none"/>
      <polygon points="20,0 470,0 395,95 230,95 140,0" fill="var(--brand-red)"/>
    </svg>
    <div class="card__photo" role="img" aria-label="Portrait photo of the broker"></div>
    <span class="card__accent" aria-hidden="true"></span>

    <section class="person">
      <h1 class="person__name">Adrian Cole</h1>
      <p class="person__role">Founder and President</p>
    </section>

    <div class="card__rule" aria-hidden="true"></div>

    <ul class="contact">
      <li class="contact__item">
        <svg viewBox="0 0 24 24" aria-hidden="true"><path d="M6.6 10.8a15 15 0 0 0 6.6 6.6l2.2-2.2c.3-.3.7-.4 1-.2 1.1.4 2.3.6 3.6.6.6 0 1 .4 1 1V20c0 .6-.4 1-1 1A17 17 0 0 1 3 4c0-.6.4-1 1-1h3.5c.6 0 1 .4 1 1 0 1.3.2 2.5.6 3.6.1.3 0 .7-.2 1z" fill="var(--brand-red)"/></svg>
        +330 5550-1470
      </li>
      <li class="contact__item">
        <svg viewBox="0 0 24 24" aria-hidden="true"><rect x="2" y="5" width="20" height="14" rx="2" fill="none" stroke="var(--brand-red)" stroke-width="2.4"/><path d="M3 6l9 7 9-7" fill="none" stroke="var(--brand-red)" stroke-width="2.4"/></svg>
        info@emberrealtyinc.com
      </li>
      <li class="contact__item">
        <svg viewBox="0 0 24 24" aria-hidden="true"><circle cx="12" cy="12" r="10" fill="var(--brand-red)"/><path d="M2 12h20M12 2c3 3 3 17 0 20M12 2c-3 3-3 17 0 20" stroke="#fff" stroke-width="1.4" fill="none"/></svg>
        www.emberrealtyinc.com
      </li>
    </ul>

    <div class="brand">
      <span class="brand__name">EMBER REALTY INC</span>
      <span class="brand__mark" aria-hidden="true"></span>
    </div>

    <address class="address" style="font-style:normal">
      1180 Maple Ridge Lane<br>
      Fairview, GA 30000
    </address>
  </main>
</body>
</html>
```